International service dog training school needs web design

We need to upgrade our website. The website is https://brightmeadow.studio/
We help trainers and service dog programs learn how to train service dogs with the latest and most ethical training methods. We offer online and in-person coaching services. We would like to see designs that are engaging and communicate professionalism, expertise, and care for the dogs and people we work with. Please also keep the colors already in the logo in the design.

```html
<!DOCTYPE html>
<html lang="en">
<head>
<meta charset="utf-8">
<title>Bright Meadow Canine Center</title>
<link href="https://fonts.googleapis.com/css2?family=Oswald:wght@400;500&family=Mulish:wght@400;500;600&display=swap" rel="stylesheet">
<style>
:root{
  --teal:#0aa59b;
  --teal-dark:#078c84;
  --blue:#1f6fc1;
  --ink:#141414;
  --body:#3a3a3a;
  --grey-bg:#ebebeb;
  --footer:#000;
  --white:#fff;
}
*{box-sizing:border-box;margin:0;padding:0}
html,body{width:1200px;height:2885px;overflow:hidden;background:var(--white)}
body{position:relative;font-family:"Mulish",sans-serif;color:var(--body)}
.abs{position:absolute}
h1,h2,h3,h4{font-weight:400}
.head{font-family:"Oswald",sans-serif;font-weight:400;color:var(--ink)}

/* top bar */
.topbar{top:0;left:0;width:1200px;height:81px;background:var(--white)}
.brand{left:112px;top:14px;display:flex;align-items:center;gap:10px}
.brand-dot{width:44px;height:44px;border-radius:50%;background:var(--blue)}
.brand-name{font-family:"Mulish",sans-serif;font-weight:600;font-size:19px;color:var(--blue);line-height:1.1}
.contact{text-align:center;font-family:"Oswald",sans-serif}
.contact .label{font-size:14px;color:#555}
.contact .value{font-size:16px;color:var(--ink);margin-top:2px}
.login{left:965px;top:18px;width:124px;height:41px;border-radius:21px;background:var(--blue);color:var(--white);font-family:"Mulish",sans-serif;font-weight:600;font-size:15px;display:flex;align-items:center;justify-content:center;gap:9px}

/* nav */
.nav{top:81px;left:0;width:1200px;height:64px;background:var(--teal)}
.nav ul{list-style:none;position:absolute;left:134px;top:0;height:64px;display:flex;align-items:center;gap:27px}
.nav li{font-family:"Oswald",sans-serif;font-size:16px;color:var(--white);letter-spacing:-.2px}
.social{position:absolute;top:12px;width:40px;height:40px;border-radius:50%;background:var(--white)}

/* hero */
.hero{top:145px;left:0;width:1200px;height:585px;background:linear-gradient(180deg,#6f7a72 0%,#5d6660 40%,#55604e 75%,#6a7a52 100%)}
.hero-shade{inset:0;background:rgba(0,0,0,.18)}
.hero-sub{top:178px;width:1200px;text-align:center;color:var(--white);font-size:21px}
.hero-title{top:218px;width:1200px;text-align:center;color:var(--white);font-family:"Oswald",sans-serif;font-weight:400;font-size:44px;letter-spacing:-.5px}
.btn{display:flex;align-items:center;justify-content:center;font-family:"Oswald",sans-serif;font-size:22px;border-radius:25px}
.btn-teal{background:var(--teal);color:var(--white)}
.btn-line{border:2px solid var(--teal);color:var(--white)}
.dots{top:516px;left:574px;display:flex;gap:6px}
.dots span{width:12px;height:12px;border-radius:50%;border:1.5px solid var(--white)}
.dots span.on{background:var(--white)}

/* offer */
.eyebrow{top:813px;width:1162px;text-align:center;color:var(--teal);font-size:17px}
.offer-title{top:843px;width:1162px;text-align:center;font-size:36px}
.offer-intro{top:900px;left:280px;width:610px;text-align:center;font-size:15px;line-height:30px}
.svc h3{font-family:"Oswald",sans-serif;font-weight:400;font-size:19px;color:var(--ink);line-height:28px}
.svc p{font-size:15px;line-height:26px;color:var(--body);margin-top:8px}
.svc.left{text-align:right}
.icon{width:52px;height:52px;border-radius:50%;background:var(--teal);display:flex;align-items:center;justify-content:center}
.puppy{left:490px;top:1020px;width:225px;height:325px;border-radius:90px 90px 40px 40px;background:radial-gradient(ellipse at 50% 40%,#f3dfb8,#e2c48f 60%,#fff 100%)}

/* band */
.band{top:1494px;left:0;width:1200px;height:312px;background:linear-gradient(180deg,#16a89f,#0d9c93)}
.band h2{top:69px;width:1200px;text-align:center;color:var(--white);font-size:38px}
.band p{top:136px;width:1200px;text-align:center;color:var(--white);font-size:18px;font-weight:600}
.btn-white{background:var(--white);color:var(--teal)}

/* book */
.book{top:1806px;left:0;width:1200px;height:648px;background:var(--grey-bg)}
.book h2{left:116px;top:200px;font-size:36px}
.book p{left:110px;top:275px;width:460px;font-size:22px;line-height:36px;color:var(--ink)}
.photo-frame{left:684px;top:104px;width:406px;height:470px;background:var(--white);box-shadow:0 2px 8px rgba(0,0,0,.15)}
.photo{left:7px;top:7px;width:392px;height:456px;background:linear-gradient(160deg,#5a6b8a 0%,#8a6a45 45%,#6b4a2c 70%,#3b3b40 100%)}
.cover{left:612px;top:224px;width:188px;height:240px;background:linear-gradient(180deg,#f4f4f4 0%,#e8e0d4 55%,#c52a2a 100%);transform:rotate(14deg);box-shadow:2px 3px 8px rgba(0,0,0,.3)}

/* footer */
.footer{top:2454px;left:0;width:1200px;height:431px;background:var(--footer);color:var(--white)}
.footer h4{font-family:"Oswald",sans-serif;font-weight:400;font-size:22px;color:var(--white)}
.footer ul{list-style:none}
.footer li{font-size:15px;line-height:30px}
.footer .txt{font-size:15px;line-height:30px}
.newsletter-input{left:811px;top:211px;width:279px;height:42px;border:1px solid #ccc;display:flex;align-items:center;justify-content:space-between;padding:0 14px;font-size:15px}
.rule{left:113px;top:343px;width:977px;height:1px;background:#333}
.copy{top:380px;width:1200px;text-align:center;font-size:15px}
</style>
</head>
<body>

<header class="abs topbar">
  <div class="abs brand"><span class="brand-dot"></span><span class="brand-name">Bright Meadow<br>Canine Center</span></div>
  <div class="abs contact" style="left:482px;top:14px;width:200px"><div class="label">Mail Us</div><div class="value">hello@brightmeadow.studio</div></div>
  <div class="abs contact" style="left:713px;top:14px;width:160px"><div class="label">Call Us</div><div class="value">555-010-2040</div></div>
  <div class="abs login">
    <svg width="12" height="14" viewBox="0 0 12 14"><circle cx="6" cy="4" r="3.2" fill="#fff"/><path d="M0 14c0-4 2.5-6 6-6s6 2 6 6z" fill="#fff"/></svg>Login
  </div>
</header>

<nav class="abs nav">
  <ul>
    <li>HOME</li><li>BMCC</li><li>THE CENTER</li><li>HELPING ORGANIZATIONS</li><li>TEACHING TRAINERS</li><li>RESEARCH CONTACT</li>
  </ul>
  <svg class="abs" style="left:829px;top:25px" width="14" height="14" viewBox="0 0 14 14"><circle cx="6" cy="6" r="4.5" stroke="#fff" stroke-width="2" fill="none"/><line x1="9.5" y1="9.5" x2="13" y2="13" stroke="#fff" stroke-width="2"/></svg>
  <span class="social" style="left:875px"></span>
  <span class="social" style="left:927px"></span>
  <span class="social" style="left:979px"></span>
  <span class="social" style="left:1031px"></span>
</nav>

<section class="abs hero">
  <div class="abs" role="img" aria-label="Photo of a border collie leaping over an agility jump" style="inset:0"></div>
  <div class="abs hero-shade"></div>
  <p class="abs hero-sub">The Bright Meadow center for service dog coaching</p>
  <h1 class="abs hero-title">COACHING FOR SERVICE DOG PROFESSIONALS</h1>
  <div class="abs btn btn-teal" style="left:421px;top:296px;width:168px;height:47px">Get Started</div>
  <div class="abs btn btn-line" style="left:610px;top:296px;width:168px;height:47px">Learn More</div>
  <div class="abs dots"><span class="on"></span><span></span><span></span></div>
</section>

<p class="abs eyebrow">Welcome</p>
<h2 class="abs head offer-title">What We Offer</h2>
<p class="abs offer-intro">Lorem ipsum dolor sit amet, consectetur adipiscing elit, sed do eiusmod tempor incididunt ut labore et dolore magna aliqua. Quis ipsum</p>

<div class="abs svc left" style="left:140px;top:1008px;width:276px"><h3>Organization/Program Consulting</h3><p>Helping organizations get started, improve their training program, and add services</p></div>
<div class="abs svc left" style="left:100px;top:1148px;width:284px"><h3>Professional coaching/teaching<br>for dog trainers</h3><p>Helping dog trainers improve their skills and learn about service dog training and medical alert dog training.</p></div>
<div class="abs svc left" style="left:136px;top:1322px;width:280px"><h3>Collaborating in Research Projects</h3><p>Collaborating in research studies in the field of Medical Detection Dogs.</p></div>

<div class="abs svc" style="left:801px;top:1004px;width:280px"><h3>Presentations and Seminars</h3><p>Sharing knowledge about service dogs and medical detection.</p></div>
<div class="abs svc" style="left:824px;top:1148px;width:270px"><h3>International services</h3><p>Fluent in both English and French, in-person and online coaching around the world.</p></div>
<div class="abs svc" style="left:803px;top:1314px;width:270px"><h3>Others</h3><p>Lorem ipsum dolor sit amet, consectetur adipiscing elit, sed do</p></div>

<div class="abs icon" style="left:436px;top:1015px"><svg width="22" height="22" viewBox="0 0 22 22"><circle cx="11" cy="11" r="10" fill="#fff"/><path d="M6.5 11l3 3 6-6" stroke="#0aa59b" stroke-width="2.4" fill="none"/></svg></div>
<div class="abs icon" style="left:404px;top:1154px"><svg width="22" height="20" viewBox="0 0 22 20"><path d="M1 1v18h20" stroke="#fff" stroke-width="2" fill="none"/><path d="M4 15l5-5 4 3 6-7" stroke="#fff" stroke-width="2" fill="none"/></svg></div>
<div class="abs icon" style="left:436px;top:1311px"><svg width="22" height="22" viewBox="0 0 22 22"><circle cx="8" cy="12" r="5" stroke="#fff" stroke-width="2.5" fill="none"/><circle cx="16" cy="6" r="3" stroke="#fff" stroke-width="2" fill="none"/></svg></div>
<div class="abs icon" style="left:707px;top:1015px"><svg width="22" height="18" viewBox="0 0 22 18"><ellipse cx="9" cy="7" rx="8" ry="6" fill="#fff"/><path d="M4 11l-2 5 6-3z" fill="#fff"/><ellipse cx="15" cy="10" rx="6" ry="4.5" fill="#fff" opacity=".85"/></svg></div>
<div class="abs icon" style="left:751px;top:1154px"><svg width="22" height="20" viewBox="0 0 22 20"><path d="M1 3l6-2 8 3 6-2v15l-6 2-8-3-6 2z" fill="#fff"/><path d="M7 1v15M15 4v15" stroke="#0aa59b" stroke-width="1.5"/></svg></div>
<div class="abs icon" style="left:722px;top:1311px"><svg width="22" height="22" viewBox="0 0 22 22"><circle cx="11" cy="11" r="8" stroke="#fff" stroke-width="2.5" fill="none"/><line x1="5.5" y1="5.5" x2="16.5" y2="16.5" stroke="#fff" stroke-width="2.5"/></svg></div>

<div class="abs puppy" role="img" aria-label="Photo of a sitting Labrador puppy"></div>

<section class="abs band" role="img" aria-label="Teal tinted photo of a seminar audience">
  <h2 class="abs head" style="color:#fff">STAYING AHEAD</h2>
  <p class="abs">Science-based and ethical training methods for the modern service dog trainer.</p>
  <div class="abs btn btn-white" style="left:516px;top:186px;width:168px;height:48px">Get Started</div>
</section>

<section class="abs book">
  <h2 class="abs head">New book from Dana Whitmore Ph.D.!</h2>
  <p class="abs">Choosing And Preparing Your Service Dog: How to Thrive in Public Access Work</p>
  <div class="abs btn btn-teal" style="left:113px;top:384px;width:168px;height:48px">Click Here</div>
  <div class="abs photo-frame"><div class="abs photo" role="img" aria-label="Photo of a German shepherd service dog in a red vest lying at its handler's feet"></div></div>
  <div class="abs cover" role="img" aria-label="Book cover showing a puppy in a red service vest"></div>
</section>

<footer class="abs footer">
  <div class="abs brand" style="left:113px;top:66px"><span class="brand-dot"></span><span class="brand-name">Bright Meadow<br>Canine Center</span></div>
  <p class="abs txt" style="left:113px;top:153px;width:270px">Lorem ipsum dolor sit amet, consectetur adipiscing elit, sed do eiusmod tempor incididunt ut labore</p>
  <h4 class="abs" style="left:417px;top:60px">Quick link</h4>
  <ul class="abs" style="left:420px;top:112px"><li>Home</li><li>BMCC</li><li>The Center</li><li>Helping organizations</li><li>Teaching Trainers</li><li>Research Contact</li></ul>
  <h4 class="abs" style="left:630px;top:60px">Help</h4>
  <ul class="abs" style="left:634px;top:112px"><li>Terms &amp; Condtions</li><li>Privacy</li><li>Policy</li><li>About Us</li><li>Support</li></ul>
  <h4 class="abs" style="left:813px;top:60px">Sign up for our newsletter</h4>
  <p class="abs" style="left:812px;top:113px;width:285px;font-size:15px;line-height:24px">Lorem ipsum dolor sit amet, consectetur adipiscing elit, sed do eiusmod tempor incididunt ut labore et dolore magna</p>
  <div class="abs newsletter-input"><span>Enter your email</span><svg width="16" height="12" viewBox="0 0 16 12"><rect x="1" y="1" width="14" height="10" rx="1.5" stroke="#fff" stroke-width="1.4" fill="none"/><path d="M1.5 1.5l6.5 5 6.5-5" stroke="#fff" stroke-width="1.4" fill="none"/></svg></div>
  <div class="abs rule"></div>
  <p class="abs copy">©Copyrights 2021&nbsp; Dana Whitmore Ph.D. &nbsp; | &nbsp; All Rights Reserved</p>
</footer>

</body>
</html>
```